VOMRA Pty Ltd Business Card

Looking for a simple yet eye-catching double-sided business card design using my company logo on one side and contact details on the other.

Target Market(s)

Government

Industry/Entity Type

Communication Systems Engineering

Contact Information for Business Card

VOMRA Pty Ltd

Requirements
Nice to have
• Would be great to have a QR code so details can be scanned into contacts

```html
<!DOCTYPE html>
<html lang="en">
<head>
<meta charset="utf-8">
<title>VOMRA Pty Ltd Business Card</title>
<link rel="stylesheet" href="https://fonts.googleapis.com/css2?family=Roboto:wght@400;500;700&display=swap">
<style>
  :root {
    --page-bg: #d9d4cc;
    --card-dark: #23272c;
    --card-dark-edge: #3a3f45;
    --card-frost: #dfe3e6;
    --card-frost-light: #f4f5f6;
    --text-light: #e6e7e8;
    --text-muted: #bfc3c7;
    --logo-silver: #dcdcdc;
    --art-silver: #b9b2a6;
    --art-dark: #1c1d1f;
  }
  * { margin: 0; padding: 0; box-sizing: border-box; }
  html, body {
    width: 1200px; height: 969px; overflow: hidden;
    background: var(--page-bg);
    font-family: "Roboto", Arial, sans-serif;
  }
  .card {
    position: absolute; left: 100px; top: 201px;
    width: 1000px; height: 566px;
    border-radius: 22px; overflow: hidden;
    background: linear-gradient(90deg,
      var(--card-dark) 0%, var(--card-dark-edge) 74.7%,
      var(--card-frost) 74.7%, var(--card-frost-light) 100%);
    box-shadow: 0 6px 24px rgba(0,0,0,0.18);
  }
  .card__logo {
    position: absolute; left: 68px; top: 84px;
    font-size: 74px; font-weight: 500; letter-spacing: 4px;
    color: var(--logo-silver); line-height: 1;
  }
  .card__name {
    position: absolute; left: 66px; top: 246px;
    font-size: 34px; font-weight: 700; color: var(--text-light);
  }
  .card__role {
    position: absolute; left: 66px; top: 290px;
    font-size: 19px; color: var(--text-muted);
  }
  .card__address {
    position: absolute; left: 67px; top: 341px;
    font-size: 21px; line-height: 31px; color: var(--text-light);
    font-style: normal;
  }
  .card__contacts {
    position: absolute; left: 68px; top: 424px;
    list-style: none;
  }
  .card__contacts li {
    display: flex; align-items: center; height: 30px;
    font-size: 21px; color: var(--text-light);
  }
  .card__contacts svg { width: 18px; height: 18px; margin-right: 16px; fill: var(--text-muted); }
  .card__art {
    position: absolute; left: 528px; top: 23px;
    width: 441px; height: 540px;
    background: linear-gradient(90deg,
      rgba(185,178,166,0.35) 0%, rgba(185,178,166,0.25) 49%,
      rgba(28,29,31,0.18) 51%, rgba(28,29,31,0.28) 100%);
    border-radius: 40% 40% 6px 6px;
  }
</style>
</head>
<body>
  <div class="card">
    <div class="card__logo">VOMRA</div>
    <div class="card__name">Daniel Brooks</div>
    <div class="card__role">Managing Director</div>
    <address class="card__address">4210 Juniper Court<br>Fairbanks, Alaska 36128</address>
    <ul class="card__contacts">
      <li>
        <svg viewBox="0 0 24 24" aria-hidden="true"><path d="M6.6 10.8a15.1 15.1 0 0 0 6.6 6.6l2.2-2.2a1 1 0 0 1 1-.25 11.4 11.4 0 0 0 3.6.57 1 1 0 0 1 1 1V20a1 1 0 0 1-1 1A17 17 0 0 1 3 4a1 1 0 0 1 1-1h3.5a1 1 0 0 1 1 1c0 1.25.2 2.45.57 3.57a1 1 0 0 1-.25 1z"/></svg>
        614-552-7830
      </li>
      <li>
        <svg viewBox="0 0 24 24" aria-hidden="true"><path d="M2 5h20v14H2zM3.5 6.5 12 13l8.5-6.5z"/></svg>
        info@veltrasys.org
      </li>
      <li>
        <svg viewBox="0 0 24 24" aria-hidden="true"><path d="M12 2a10 10 0 1 0 0 20 10 10 0 0 0 0-20zm6.9 6h-3a15.6 15.6 0 0 0-1.3-4A8 8 0 0 1 18.9 8zM12 4c.8 1.2 1.5 2.5 1.9 4h-3.8c.4-1.5 1.1-2.8 1.9-4zM4.3 14a8 8 0 0 1 0-4h3.4a16 16 0 0 0 0 4zm.8 2h3a15.6 15.6 0 0 0 1.3 4A8 8 0 0 1 5.1 16zm3-8h-3a8 8 0 0 1 4.3-4A15.6 15.6 0 0 0 8.1 8zM12 20c-.8-1.2-1.5-2.5-1.9-4h3.8c-.4 1.5-1.1 2.8-1.9 4zm2.3-6H9.7a14 14 0 0 1 0-4h4.6a14 14 0 0 1 0 4zm.3 6a15.6 15.6 0 0 0 1.3-4h3a8 8 0 0 1-4.3 4zm1.7-6a16 16 0 0 0 0-4h3.4a8 8 0 0 1 0 4z"/></svg>
        www.veltrasys.org
      </li>
    </ul>
    <div class="card__art" role="img" aria-label="Circuit-board tree illustration, silver traces on the dark half and black traces on the frosted half"></div>
  </div>
</body>
</html>
```